K7 Electrical Services Ltd Web design

I require a web site for my new electrical contracting company. We are customer service orientated. Offering high value electrical installations, design and maintenance. Focused on custom residential and commercial upgrading. Lighting design and application are paramount in our company's services. Industry leading product use and integration are always on the forefront with our customer client services. As well as energy efficiency.

Target Market(s)

Homebuilders, General Contractors, Property management companies, clients, individuals,

Industry/Entity Type

Electric Company

Coding

Coded - Design and coding required

Number of Pages Required

3 page

Requirements
Must have
• Classic, modern, edgy but not trendy . Appeals to the masse.
• 3 page
• home page
• about page
• gallery page
• ability to contact from the webiste
Nice to have
• open to all types of designs that are relative to the construction industry.
• Black, Grey, metallic ice blue and deep purple colours from the logo.
Should not have
• anything cheesy with cartoon light bulb images.

```html
<!DOCTYPE html>
<html lang="en">
<head>
<meta charset="utf-8">
<title>K7 Electrical Services Ltd</title>
<link href="https://fonts.googleapis.com/css2?family=Roboto:wght@400;500;700&family=Open+Sans:wght@400;600&display=swap" rel="stylesheet">
<style>
:root{
  --purple:#6b2f93;
  --purple-dark:#4a1f6a;
  --purple-deep:#2e1442;
  --ink:#2b2b2b;
  --text:#777;
  --line:#e3e3e3;
  --white:#fff;
  --footer:#fafafa;
}
*{box-sizing:border-box;margin:0;padding:0}
html,body{width:1200px;height:2904px;overflow:hidden}
body{font-family:"Open Sans",Arial,sans-serif;color:var(--text);background:var(--white);font-size:14px;line-height:1.6}
h1,h2,h3,h4,.nav,.btn,.brand-name{font-family:"Roboto",Arial,sans-serif}
a{color:inherit;text-decoration:none}
.btn{display:inline-block;font-size:12px;font-weight:500;letter-spacing:1px;text-transform:uppercase;border-radius:20px;padding:9px 24px}
.btn-ghost{border:2px solid var(--white);color:var(--white)}
.btn-link{color:var(--purple);font-size:11px;font-weight:700;padding:0;letter-spacing:.5px}

/* header */
.site-header{position:relative;height:88px;border-bottom:1px solid var(--line)}
.topbar{position:absolute;right:0;top:0;height:30px;width:470px;background:var(--purple-deep);color:#ddd;font-size:12px;display:flex;align-items:center;justify-content:flex-end;gap:26px;padding-right:40px;clip-path:polygon(24px 0,100% 0,100% 100%,0 100%)}
.topbar span{display:flex;align-items:center;gap:7px}
.brand{position:absolute;left:96px;top:30px;display:flex;align-items:center;gap:10px}
.brand-mark{width:16px;height:16px;background:var(--purple)}
.brand-name{font-weight:500;font-size:20px;color:var(--purple);line-height:1.2}
.nav{position:absolute;right:90px;top:48px;display:flex;gap:30px;font-size:13px;font-weight:500;color:var(--ink);text-transform:uppercase}
.nav .active{color:var(--purple)}

/* hero */
.hero{position:relative;height:508px;background:linear-gradient(180deg,#6d4e8c 0%,#8a5a8e 35%,#3e2a55 70%,#241a38 100%);text-align:center;color:var(--white)}
.hero h1{padding-top:160px;font-size:54px;font-weight:700;letter-spacing:1px;line-height:1.3}
.hero p{font-size:24px;margin:4px 0 30px}
.hero-arrows{position:absolute;left:50%;bottom:14px;transform:translateX(-50%);display:flex;gap:6px}
.hero-arrows span{width:30px;height:30px;background:var(--white);display:flex;align-items:center;justify-content:center}

/* welcome */
.welcome{height:560px;text-align:center;padding-top:64px}
.section-title{font-size:34px;font-weight:700;color:var(--ink);letter-spacing:.5px}
.welcome .intro{width:760px;margin:24px auto 0;font-size:13px}
.services{display:flex;justify-content:center;gap:36px;margin-top:60px}
.service{width:304px;height:230px;border:1px solid var(--line);position:relative;padding-top:70px}
.service-icon{position:absolute;left:50%;top:-34px;transform:translateX(-50%);width:68px;height:68px;border-radius:50%;border:2px solid var(--purple);background:var(--white);display:flex;align-items:center;justify-content:center}
.service h3{font-size:20px;font-weight:500;color:var(--ink);margin-bottom:10px}
.service p{font-size:13px;padding:0 36px;margin-bottom:16px}

/* focus band */
.focus{position:relative;height:316px;display:flex;color:var(--white)}
.focus-half{width:50%;padding:70px 0 0 96px}
.focus-res{background:linear-gradient(90deg,#5b2682,#7a3ca3)}
.focus-com{background:linear-gradient(90deg,#8d6bb0,#b8a3cc);padding-left:170px}
.focus h2{font-size:36px;font-weight:700;letter-spacing:1px}
.focus p{font-size:13px;width:380px;margin:8px 0 22px}
.focus-badge{position:absolute;left:50%;top:50%;transform:translate(-50%,-50%);width:150px;height:150px;border-radius:50%;background:var(--white);color:var(--ink);font-family:"Roboto",sans-serif;font-weight:700;font-size:22px;display:flex;align-items:center;justify-content:center;text-align:center;line-height:1.2;border:8px solid #e9e1f0}

/* news */
.news{height:620px;padding-top:66px;text-align:center}
.news-grid{display:flex;justify-content:center;gap:36px;margin-top:56px;text-align:left}
.news-card{width:304px}
.news-img{height:164px}
.img-warehouse{background:linear-gradient(180deg,#cfd3d6,#8f979c)}
.img-wiring{background:linear-gradient(135deg,#e8d8c8,#b9a08a)}
.img-panel{background:linear-gradient(135deg,#c9ced2,#7e878d)}
.news-card h3{font-size:20px;font-weight:500;color:var(--ink);margin:28px 0 8px}
.meta{font-size:11px;color:#999;border-bottom:1px solid var(--line);padding-bottom:8px;margin-bottom:10px;display:flex;gap:20px}
.news-card p{font-size:12px;margin-bottom:14px}

/* why */
.why{height:440px;display:flex}
.why-img{width:600px;background:linear-gradient(135deg,#dcdcdc,#8a8a8a 60%,#4b4b4b)}
.why-body{width:600px;background:linear-gradient(135deg,#6b2f93,#4a1f6a);color:var(--white);padding:44px 0 0 70px}
.why-body h2{font-size:34px;font-weight:700}
.why-body .lead{font-size:13px;width:400px;margin:14px 0 18px;color:#e6dced}
.why-list{list-style:none;font-size:13px}
.why-list li{display:flex;align-items:center;gap:10px;margin-bottom:8px}
.why-body .btn{margin-top:18px}

/* footer */
.site-footer{height:372px;background:var(--footer);position:relative}
.footer-cols{display:flex;padding:52px 0 0 96px}
.footer-brand{width:330px;padding-top:56px;display:flex;align-items:center;gap:10px}
.footer-brand .brand-name{font-size:24px}
.footer-col{width:240px}
.footer-col h4{font-size:14px;font-weight:700;color:var(--ink);text-transform:uppercase;margin-bottom:14px}
.footer-col ul{list-style:none;font-size:12px;line-height:1.9}
.footer-col p{font-size:12px}
.field{height:34px;border:1px solid var(--line);background:var(--white);margin:14px 0;font-size:11px;color:#aaa;padding:8px 12px;width:210px}
.btn-solid{background:var(--purple);color:var(--white);padding:7px 20px;font-size:11px}
.contact-line{display:flex;gap:10px;font-size:12px;margin-bottom:10px;align-items:flex-start}
.footer-bottom{position:absolute;left:96px;right:96px;bottom:0;height:56px;border-top:1px solid var(--line);display:flex;align-items:center;justify-content:space-between;font-size:11px}
.socials{display:flex;gap:6px}
.socials span{width:26px;height:26px;border-radius:50%;background:var(--purple)}
</style>
</head>
<body>

<header class="site-header">
  <div class="topbar">
    <span><svg width="12" height="12" viewBox="0 0 24 24"><path fill="#ddd" d="M6.6 10.8a15 15 0 0 0 6.6 6.6l2.2-2.2a1 1 0 0 1 1-.3 11 11 0 0 0 3.6.6 1 1 0 0 1 1 1V20a1 1 0 0 1-1 1A17 17 0 0 1 3 4a1 1 0 0 1 1-1h3.5a1 1 0 0 1 1 1c0 1.2.2 2.4.6 3.6a1 1 0 0 1-.3 1z"/></svg>1 555 014 2290</span>
    <span><svg width="13" height="10" viewBox="0 0 24 18"><rect x="1" y="1" width="22" height="16" fill="none" stroke="#ddd" stroke-width="2"/><path d="M1 1l11 9 11-9" fill="none" stroke="#ddd" stroke-width="2"/></svg>info@k7electrical.com</span>
  </div>
  <a class="brand" href="#"><span class="brand-mark"></span><span class="brand-name">K7 Electrical Services Ltd</span></a>
  <nav class="nav"><a class="active">Home</a><a>About Us</a><a>Services</a><a>Projects</a><a>News</a><a>Careers</a><a>Contact</a></nav>
</header>

<section class="hero" role="img" aria-label="Night-time city skyline photograph in purple tones">
  <h1>K7 ELECTRICAL</h1>
  <p>We are a new electrical contracting company</p>
  <a class="btn btn-ghost">Get Info</a>
  <div class="hero-arrows">
    <span><svg width="10" height="12" viewBox="0 0 10 12"><path d="M8 1L2 6l6 5" fill="none" stroke="#333" stroke-width="2"/></svg></span>
    <span><svg width="10" height="12" viewBox="0 0 10 12"><path d="M2 1l6 5-6 5" fill="none" stroke="#333" stroke-width="2"/></svg></span>
  </div>
</section>

<section class="welcome">
  <h2 class="section-title">WELCOME TO K7 ELECTRICAL</h2>
  <p class="intro">We are customer service orientated. Offering high value electrical installations, design and maintenance. Focused on custom residential and commercial upgrading. Lighting design and application are paramount in our company's services.</p>
  <div class="services">
    <div class="service">
      <div class="service-icon"><svg width="30" height="30" viewBox="0 0 24 24"><circle cx="12" cy="12" r="7" fill="none" stroke="#6b2f93" stroke-width="2.5" stroke-dasharray="3 2.5"/><circle cx="12" cy="12" r="3" fill="none" stroke="#6b2f93" stroke-width="2"/></svg></div>
      <h3>Electrical Installations</h3>
      <p>Focused on custom residential and commercial upgrading.</p>
      <a class="btn btn-link">Read More</a>
    </div>
    <div class="service">
      <div class="service-icon"><svg width="28" height="28" viewBox="0 0 24 24"><rect x="3" y="5" width="15" height="16" fill="none" stroke="#6b2f93" stroke-width="2"/><path d="M10 14l9-9 2 2-9 9h-2z" fill="#6b2f93"/></svg></div>
      <h3>Electrical Design</h3>
      <p>Focused on custom residential and commercial upgrading.</p>
      <a class="btn btn-link">Read More</a>
    </div>
    <div class="service">
      <div class="service-icon"><svg width="28" height="28" viewBox="0 0 24 24"><path d="M14.5 3a5 5 0 0 0-4.6 6.9L3 16.8 7.2 21l6.9-6.9A5 5 0 0 0 21 9.5l-3 3-3.5-1-1-3.5 3-3A5 5 0 0 0 14.5 3z" fill="#6b2f93"/></svg></div>
      <h3>Maintenance</h3>
      <p>Focused on custom residential and commercial upgrading.</p>
      <a class="btn btn-link">Read More</a>
    </div>
  </div>
</section>

<section class="focus">
  <div class="focus-half focus-res">
    <h2>RESIDENTIAL</h2>
    <p>Lighting design and application are paramount in our company's services. Industry leading product use and integration always at the forefront.</p>
    <a class="btn btn-ghost">Read More</a>
  </div>
  <div class="focus-half focus-com" role="img" aria-label="Commercial building interior photograph under a purple tint">
    <h2>COMMERCIAL</h2>
    <p>Lighting design and application are paramount in our company's services. Industry leading product use and integration always at the forefront.</p>
    <a class="btn btn-ghost">Read More</a>
  </div>
  <div class="focus-badge">FOCUSED<br>ON</div>
</section>

<section class="news">
  <h2 class="section-title">LATEST NEWS</h2>
  <div class="news-grid">
    <article class="news-card">
      <div class="news-img img-warehouse" role="img" aria-label="Warehouse ceiling lighting photograph"></div>
      <h3>Finibus Bonorum et Malorum</h3>
      <div class="meta"><span>23/09/2017</span><span>Admin</span></div>
      <p>Neque porro quisquam est qui dolorem ipsum quia dolor sit amet, consectetur, adipisci velit sed quia non.</p>
      <a class="btn btn-link">Read More</a>
    </article>
    <article class="news-card">
      <div class="news-img img-wiring" role="img" aria-label="Hands wiring a circuit breaker panel photograph"></div>
      <h3>Finibus Bonorum et Malorum</h3>
      <div class="meta"><span>23/09/2017</span><span>Admin</span></div>
      <p>Neque porro quisquam est qui dolorem ipsum quia dolor sit amet, consectetur, adipisci velit sed quia non.</p>
      <a class="btn btn-link">Read More</a>
    </article>
    <article class="news-card">
      <div class="news-img img-panel" role="img" aria-label="Electrical meter and panel photograph"></div>
      <h3>Finibus Bonorum et Malorum</h3>
      <div class="meta"><span>23/09/2017</span><span>Admin</span></div>
      <p>Neque porro quisquam est qui dolorem ipsum quia dolor sit amet, consectetur, adipisci velit sed quia non.</p>
      <a class="btn btn-link">Read More</a>
    </article>
  </div>
</section>

<section class="why">
  <div class="why-img" role="img" aria-label="Hand sketching a circuit board diagram"></div>
  <div class="why-body">
    <h2>WHY CHOOSE US</h2>
    <p class="lead">Neque porro quisquam est, qui dolorem ipsum quia dolor sit amet, consectetur adipisci velit sed quia.</p>
    <ul class="why-list">
      <li><svg width="16" height="16" viewBox="0 0 16 16"><circle cx="8" cy="8" r="7.5" fill="#fff"/><path d="M4.5 8.2l2.3 2.3 4.7-4.8" fill="none" stroke="#6b2f93" stroke-width="1.8"/></svg>Value all quotes and our service to every client</li>
      <li><svg width="16" height="16" viewBox="0 0 16 16"><circle cx="8" cy="8" r="7.5" fill="#fff"/><path d="M4.5 8.2l2.3 2.3 4.7-4.8" fill="none" stroke="#6b2f93" stroke-width="1.8"/></svg>Licensed, insured and fully certified electricians</li>
      <li><svg width="16" height="16" viewBox="0 0 16 16"><circle cx="8" cy="8" r="7.5" fill="#fff"/><path d="M4.5 8.2l2.3 2.3 4.7-4.8" fill="none" stroke="#6b2f93" stroke-width="1.8"/></svg>Dependable timelines with clear communication</li>
      <li><svg width="16" height="16" viewBox="0 0 16 16"><circle cx="8" cy="8" r="7.5" fill="#fff"/><path d="M4.5 8.2l2.3 2.3 4.7-4.8" fill="none" stroke="#6b2f93" stroke-width="1.8"/></svg>Energy efficient lighting and product integration</li>
      <li><svg width="16" height="16" viewBox="0 0 16 16"><circle cx="8" cy="8" r="7.5" fill="#fff"/><path d="M4.5 8.2l2.3 2.3 4.7-4.8" fill="none" stroke="#6b2f93" stroke-width="1.8"/></svg>Support for builders and property managers</li>
    </ul>
    <a class="btn btn-ghost">Read More</a>
  </div>
</section>

<footer class="site-footer">
  <div class="footer-cols">
    <div class="footer-brand"><span class="brand-mark"></span><span class="brand-name">K7 Electrical Services Ltd</span></div>
    <div class="footer-col">
      <h4>Quick Links</h4>
      <ul><li>Help</li><li>FAQ</li><li>Support</li><li>Sitemap</li><li>Terms Of Use</li><li>Privacy Statement</li></ul>
    </div>
    <div class="footer-col" style="width:290px">
      <h4>Newsletter Subscription</h4>
      <p>Register your email address to get information about us.</p>
      <div class="field">Your email address</div>
      <a class="btn btn-solid">Subscribe</a>
    </div>
    <div class="footer-col">
      <h4>Contact Us</h4>
      <div class="contact-line"><svg width="12" height="14" viewBox="0 0 12 16"><path d="M6 0a6 6 0 0 0-6 6c0 4.5 6 10 6 10s6-5.5 6-10a6 6 0 0 0-6-6zm0 8.5A2.5 2.5 0 1 1 6 3.5a2.5 2.5 0 0 1 0 5z" fill="#6b2f93"/></svg><span>1248 Meridian Road,<br>Halton, ON L7K 2P4</span></div>
      <div class="contact-line"><svg width="12" height="12" viewBox="0 0 24 24"><path fill="#6b2f93" d="M6.6 10.8a15 15 0 0 0 6.6 6.6l2.2-2.2a1 1 0 0 1 1-.3 11 11 0 0 0 3.6.6 1 1 0 0 1 1 1V20a1 1 0 0 1-1 1A17 17 0 0 1 3 4a1 1 0 0 1 1-1h3.5a1 1 0 0 1 1 1c0 1.2.2 2.4.6 3.6a1 1 0 0 1-.3 1z"/></svg><span>1 555 014 2290</span></div>
      <div class="contact-line"><svg width="13" height="10" viewBox="0 0 24 18"><rect x="1" y="1" width="22" height="16" fill="none" stroke="#6b2f93" stroke-width="2"/><path d="M1 1l11 9 11-9" fill="none" stroke="#6b2f93" stroke-width="2"/></svg><span>info@k7electrical.com</span></div>
    </div>
  </div>
  <div class="footer-bottom">
    <span>Copyright © 2017 K7 Electrical Services Ltd. All rights reserved.</span>
    <div class="socials"><span></span><span></span><span></span><span></span></div>
  </div>
</footer>

</body>
</html>
```